My Web Development Portfolio site

I'm a web developer and I need a web design that can showcase my web development portfolio. I like most of the websites from this link: http://www.lumivexa.com/portfolios/examples-503917. My ideal design should be modern, clean and fun. I will let the designer decided the color theme for the website.

Target Market(s)

Potential Employers.

Number of Pages Required

1 page

Requirements
Must have
• - Menu bar that includes at least: About Me, Blog, Contact, Project/Work
• - Excellent color theme
• - Use the logo I provided (see attachment)
Nice to have
• - Some animation
• - Fun yet modern design

```html
<!DOCTYPE html>
<html lang="en">
<head>
<meta charset="utf-8">
<title>pixelforge — Marlo Finch, Web Developer</title>
<link rel="stylesheet" href="https://fonts.googleapis.com/css2?family=Raleway:wght@300;400;600;700&family=Lato:wght@400;700&display=swap">
<style>
  :root {
    --ink: #000000;
    --panel: #0b0b0b;
    --white: #ffffff;
    --soft: #d6d6d6;
    --muted: #8a8a8a;
    --rule: #3a3a3a;
    --orange: #f47a36;
    --teal-dark: #123a3d;
    --teal: #1f5457;
    --desk: #6b4428;
  }
  * { margin: 0; padding: 0; box-sizing: border-box; }
  html, body { width: 1200px; height: 3364px; overflow: hidden; background: var(--ink); }
  body { position: relative; font-family: "Lato", sans-serif; color: var(--white); }
  .abs { position: absolute; }

  /* Hero */
  .hero { left: 0; top: 0; width: 1200px; height: 706px; overflow: hidden; }
  .hero-scene {
    position: absolute; inset: 0;
    background:
      linear-gradient(180deg, transparent 0 560px, var(--desk) 560px 706px),
      radial-gradient(ellipse 320px 260px at 600px 380px, #2c6a62 0%, transparent 70%),
      linear-gradient(180deg, var(--teal) 0%, var(--teal-dark) 100%);
  }
  .hero-social { left: 80px; top: 34px; display: flex; gap: 14px; }
  .hero-social span, .foot-social span { width: 20px; height: 20px; border-radius: 50%; background: var(--white); display: block; }
  .menu-toggle { left: 1083px; top: 32px; width: 36px; height: 28px; }
  .brand { left: 0; top: 68px; width: 1200px; text-align: center; }
  .brand-mark { width: 86px; height: 86px; border: 7px solid var(--white); border-radius: 50%; margin: 0 auto 10px; }
  .brand-name { font-family: "Raleway", sans-serif; font-weight: 300; font-size: 58px; letter-spacing: 2px; line-height: 1; }
  .slide-arrow { top: 304px; width: 50px; height: 44px; background: #2b2b2b; display: flex; align-items: center; justify-content: center; }
  .slide-arrow.prev { left: 31px; }
  .slide-arrow.next { left: 1119px; }
  .avatar { left: 521px; top: 398px; width: 156px; height: 156px; border-radius: 50%; border: 5px solid var(--white);
    background: radial-gradient(circle at 50% 45%, #c9a08a 0%, #7d5b4a 60%, #3c3a38 100%); }
  .hero-name { left: 0; top: 578px; width: 1200px; text-align: center; font-family: "Raleway", sans-serif; font-size: 25px; font-weight: 400; }
  .hero-name b { font-weight: 600; }
  .hero-rule { left: 410px; top: 614px; width: 382px; height: 1px; background: rgba(255,255,255,.45); }
  .hero-role { left: 0; top: 628px; width: 1200px; text-align: center; font-family: "Raleway", sans-serif; font-size: 36px; color: var(--orange); font-weight: 300; }
  .hero-role b { font-weight: 700; }

  /* Section headings */
  .section-title { font-family: "Raleway", sans-serif; font-weight: 300; font-size: 40px; color: var(--orange); line-height: 1; }
  .section-title b { font-weight: 600; }
  .title-rule { height: 2px; background: var(--rule); }
  .title-rule::before { content: ""; position: absolute; left: 0; top: -1px; width: 100px; height: 3px; background: var(--orange); }

  /* Portfolio */
  .work-tile { width: 328px; height: 540px; overflow: hidden; }
  .work-shot { position: absolute; inset: 0; }
  .tile-overlay { position: absolute; left: 0; bottom: 0; width: 100%; height: 224px; background: rgba(0,0,0,.88); text-align: center; padding: 48px 26px 0; }
  .tile-overlay p { font-size: 16px; line-height: 24px; color: var(--white); }
  .tile-actions { display: flex; gap: 30px; margin: 26px 0 0 16px; }
  .btn { height: 42px; display: flex; align-items: center; justify-content: center; font-size: 16px; gap: 8px; }
  .btn-zoom { width: 106px; border: 2px solid var(--white); }
  .btn-visit { width: 106px; background: var(--orange); }
  .work-tile.active { box-shadow: 0 0 18px rgba(255,255,255,.35); }

  /* About */
  .about-body { left: 81px; top: 2730px; width: 470px; font-size: 16px; line-height: 26px; color: var(--soft); }
  .about-body .label { color: var(--orange); font-weight: 700; display: inline-block; width: 90px; }
  .about-body .label-solo { color: var(--orange); font-weight: 700; }
  .about-body strong { color: var(--white); }
  .ticks { list-style: none; }
  .ticks li { display: flex; align-items: center; gap: 10px; }

  /* Blog */
  .blog-nav { left: 1083px; top: 2664px; font-size: 22px; color: var(--soft); letter-spacing: 10px; }
  .post { left: 646px; width: 480px; display: flex; gap: 16px; }
  .post-thumb { width: 128px; height: 90px; flex: none; }
  .post h3 { font-size: 16px; font-weight: 700; line-height: 20px; }
  .post p { font-size: 14px; line-height: 19px; color: var(--soft); margin-top: 4px; }
  .post a { font-size: 13px; color: var(--orange); text-decoration: underline; font-style: italic; }

  /* Contact */
  .contact-title { left: 0; top: 2972px; width: 1200px; text-align: center; }
  .contact-rule { left: 516px; top: 3025px; width: 527px; height: 2px; background: var(--rule); }
  .contact-lead { left: 0; top: 3062px; width: 1200px; text-align: center; font-family: "Raleway", sans-serif; font-weight: 700; font-size: 28px; }
  .contact-sub { left: 0; top: 3098px; width: 1200px; text-align: center; font-size: 14px; color: var(--soft); }
  .contact-btn { left: 453px; top: 3133px; width: 294px; height: 76px; border: 2px solid var(--orange); border-radius: 6px;
    display: flex; align-items: center; justify-content: center; gap: 14px; font-family: "Raleway", sans-serif; font-size: 24px; }
  .foot-social { left: 0; top: 3236px; width: 1200px; display: flex; justify-content: center; gap: 18px; }
  .foot-social span { background: var(--soft); }
  .copyright { left: 0; top: 3282px; width: 1200px; text-align: center; font-size: 12px; color: var(--muted); }
</style>
</head>
<body>

<header class="abs hero">
  <div class="hero-scene" role="img" aria-label="Illustration of a developer seated at a desk facing a monitor, wall clock in the corner"></div>
  <nav class="abs hero-social" aria-label="Social links">
    <span></span><span></span><span></span><span></span><span></span>
  </nav>
  <svg class="abs menu-toggle" viewBox="0 0 36 28" aria-label="Menu"><rect y="2" width="36" height="3" fill="#fff"/><rect y="10" width="36" height="3" fill="#fff"/><rect y="18" width="36" height="3" fill="#fff"/><rect y="25" width="36" height="3" fill="#fff"/></svg>
  <div class="abs brand">
    <div class="brand-mark"></div>
    <div class="brand-name">pixelforge</div>
  </div>
  <div class="abs slide-arrow prev"><svg width="14" height="18" viewBox="0 0 14 18"><path d="M11 2 L4 9 L11 16" stroke="#fff" stroke-width="3" fill="none"/></svg></div>
  <div class="abs slide-arrow next"><svg width="14" height="18" viewBox="0 0 14 18"><path d="M3 2 L10 9 L3 16" stroke="#fff" stroke-width="3" fill="none"/></svg></div>
  <div class="abs avatar" role="img" aria-label="Portrait photo of Marlo Finch"></div>
  <div class="abs hero-name">Marlo <b>Finch</b></div>
  <div class="abs hero-rule"></div>
  <div class="abs hero-role">I am a <b>Web Developer</b></div>
</header>

<main>
  <h2 class="abs section-title" style="left:81px; top:765px;">Web <b>Portfolio</b></h2>
  <div class="abs title-rule" style="left:81px; top:823px; width:1036px;"></div>

  <section aria-label="Portfolio">
    <div class="abs work-tile" style="left:81px; top:870px;"><div class="work-shot" role="img" aria-label="Website screenshot: studio portfolio with product photos" style="background:linear-gradient(180deg,#8a9bb0 0 35%,#f2f2f2 35% 94%,#cfeee4 94%);"></div></div>
    <div class="abs work-tile" style="left:435px; top:870px;"><div class="work-shot" role="img" aria-label="Website screenshot: juice cleanse landing page" style="background:linear-gradient(180deg,#f4f4f4 0 26%,#f3c64a 26% 42%,#9fcf5e 42% 68%,#b07fc0 68% 84%,#8fd0e0 84%);"></div></div>
    <div class="abs work-tile" style="left:790px; top:870px;"><div class="work-shot" role="img" aria-label="Website screenshot: agency page with teal banner" style="background:linear-gradient(180deg,#2d2d2d 0 3%,#4cc4cf 3% 30%,#f5f5f5 30%);"></div></div>

    <div class="abs work-tile active" style="left:81px; top:1467px;">
      <div class="work-shot" role="img" aria-label="Website screenshot: grocery shop page" style="background:linear-gradient(180deg,#f1f4ec 0 38%,#2f9a64 38% 70%,#1a1a1a 70%);"></div>
      <div class="tile-overlay">
        <p>Lorem ipsum dolor sit amet, consectetur adipiscing elit. Sed vitae magna tellus. Aenean ante nunc.</p>
        <div class="tile-actions">
          <div class="btn btn-zoom"><svg width="18" height="18" viewBox="0 0 18 18"><circle cx="7.5" cy="7.5" r="5.5" stroke="#fff" stroke-width="2" fill="none"/><path d="M11.5 11.5 L16 16" stroke="#fff" stroke-width="2"/></svg>Zoom</div>
          <div class="btn btn-visit">Visit Web</div>
        </div>
      </div>
    </div>
    <div class="abs work-tile" style="left:435px; top:1467px;"><div class="work-shot" role="img" aria-label="Website screenshot: blue creative agency page" style="background:linear-gradient(180deg,#1c8fb5 0 26%,#f6f6f6 26% 56%,#2aa7c9 56% 68%,#f0f0f0 68%);"></div></div>
    <div class="abs work-tile" style="left:790px; top:1467px;"><div class="work-shot" role="img" aria-label="Website screenshot: music artist page" style="background:linear-gradient(180deg,#1d1d1d 0 30%,#3f86b7 30% 84%,#111 84%);"></div></div>

    <div class="abs work-tile" style="left:81px; top:2064px;"><div class="work-shot" role="img" aria-label="Website screenshot: app template page" style="background:linear-gradient(180deg,#3a3a3a 0 24%,#ffffff 24%);"></div></div>
    <div class="abs work-tile" style="left:435px; top:2064px;"><div class="work-shot" role="img" aria-label="Website screenshot: city skyline business page" style="background:linear-gradient(180deg,#8c7a66 0 22%,#f3f3f3 22% 48%,#e8e8e8 48% 90%,#3fa7a3 90%);"></div></div>
    <div class="abs work-tile" style="left:790px; top:2064px;"><div class="work-shot" role="img" aria-label="Website screenshot: studio template with skyline" style="background:linear-gradient(180deg,#b79173 0 30%,#f6f6f6 30% 78%,#4aa89a 78% 92%,#f6f6f6 92%);"></div></div>
  </section>

  <section aria-label="About me">
    <h2 class="abs section-title" style="left:81px; top:2660px;">About <b>Me</b></h2>
    <div class="abs title-rule" style="left:81px; top:2712px; width:471px;"></div>
    <div class="abs about-body">
      <div><span class="label">Name :</span><strong>Marlo Finch - <b>I am a Web Developer</b></strong></div>
      <div class="label-solo">Expertise :</div>
      <p>Lorem ipsum dolor sit amet, consectetur adipiscing elit. Cras elementum eleifend erat vitae.</p>
      <ul class="ticks">
        <li><svg width="16" height="14" viewBox="0 0 16 14"><path d="M1 7 L6 12 L15 1" stroke="#f47a36" stroke-width="3" fill="none"/></svg>Lorem ipsum dolor sit &nbsp;consectetur</li>
        <li><svg width="16" height="14" viewBox="0 0 16 14"><path d="M1 7 L6 12 L15 1" stroke="#f47a36" stroke-width="3" fill="none"/></svg>Lorem ipsum dolor sit &nbsp;consectetur</li>
      </ul>
    </div>
  </section>

  <section aria-label="Blog">
    <h2 class="abs section-title" style="left:646px; top:2660px;">Blog <b>Post</b></h2>
    <div class="abs blog-nav">‹›</div>
    <div class="abs title-rule" style="left:646px; top:2712px; width:471px;"></div>
    <article class="abs post" style="top:2725px;">
      <div class="post-thumb" role="img" aria-label="Blog thumbnail: chalkboard lettering artwork" style="background:linear-gradient(135deg,#2b2b2b,#555);"></div>
      <div><h3>Lorem ipsum dolor sit amet</h3><p>Lorem ipsum dolor sit amet, consectetur adipiscing elit. Cras elementum eleifend erat vitae.</p><a>Read More</a></div>
    </article>
    <article class="abs post" style="top:2831px;">
      <div class="post-thumb" role="img" aria-label="Blog thumbnail: glowing speedometer artwork" style="background:linear-gradient(135deg,#0d2a44,#c0612a);"></div>
      <div><h3>Lorem ipsum dolor sit amet</h3><p>Lorem ipsum dolor sit amet, consectetur adipiscing elit. Cras elementum eleifend erat vitae.</p><a>Read More</a></div>
    </article>
  </section>

  <section aria-label="Contact">
    <h2 class="abs section-title contact-title">Contact</h2>
    <div class="abs contact-rule"></div>
    <div class="abs contact-lead">Let's work together</div>
    <div class="abs contact-sub">I'm currently accepting select design projects.</div>
    <div class="abs contact-btn"><svg width="30" height="26" viewBox="0 0 30 26"><rect x="2" y="2" width="26" height="22" rx="3" stroke="#fff" stroke-width="2" fill="none"/><path d="M2 12 H10 L12 16 H18 L20 12 H28" stroke="#fff" stroke-width="2" fill="none"/></svg>Contact Me Now</div>
  </section>
</main>

<footer>
  <nav class="abs foot-social" aria-label="Social links"><span></span><span></span><span></span><span></span><span></span></nav>
  <div class="abs copyright">Copyright @ 2016 pixelforge.&nbsp; All Rights Reserved.</div>
</footer>

</body>
</html>
```